To promote our Catering Equipment services to our Laundry customers

Our company specialises in the supply, installation & maintenance of commercial laundry equipment, and we want a flyer that can be handed out to our laundry equipment customers to promote the fact that we also supply, rent, repair & service catering equipment as well (Catering equipment such as Cookers, Ovens etc)

Target Market(s)

The target market will be our existing customers. They trust us to repair their laundry equipment... why not trust us to do their catering equipment as well? Our customers are all business customers such as Care Homes for the elderly, Hotels etc.

Industry/Entity Type

Catering

Requirements
Must have
• Flyer will be approx. 216 x 139mm (To be confirmed) once we have a printer.
• It must include the www.brantleyservices-example.co.uk website address & our contact telephone number 0116 583 2901.
Nice to have
• Ideally it would pitch us a ' a one-stop shop' for all of their catering & laundry equipment needs.
• It might be better to be styled along a similar colour scheme as our website at www.brantleyservices-example.co.uk.

```html
<!DOCTYPE html>
<html lang="en">
<head>
<meta charset="utf-8">
<title>Brantley Services – Commercial Laundry &amp; Dishwasher Flyer</title>
<link rel="stylesheet" href="https://fonts.googleapis.com/css2?family=Questrial&family=Source+Sans+3:wght@400;700&display=swap">
<style>
  :root {
    --brand-red: #e3202b;
    --brand-blue: #1a5ea8;
    --ink-grey: #555759;
    --body-grey: #6a6b6d;
    --band-grey: #e7e7e8;
    --paper: #ffffff;
    --seal-neutral: #d6d7d9;
    --steel-light: #c9cbcd;
    --steel-dark: #6f7376;
  }
  * { box-sizing: border-box; margin: 0; padding: 0; }
  html, body { width: 869px; height: 1200px; overflow: hidden; background: var(--paper); }
  .flyer { position: relative; width: 869px; height: 1200px; background: var(--paper); overflow: hidden; }

  .brand-name {
    position: absolute; left: 55px; top: 40px;
    display: flex; align-items: center; gap: 10px;
    font-family: "Source Sans 3", sans-serif; font-weight: 700;
    font-size: 30px; color: var(--brand-red); letter-spacing: 0.3px;
  }
  .brand-name .mark { width: 22px; height: 22px; background: var(--brand-red); }

  .title {
    position: absolute; left: 53px; top: 132px;
    font-family: "Questrial", sans-serif; font-weight: 400;
    font-size: 47px; line-height: 58px; color: var(--ink-grey);
  }
  .title .accent { color: var(--brand-red); display: block; }

  .photo { position: absolute; }
  .photo-home-kitchen {
    left: 639px; top: 0; width: 230px; height: 271px;
    background: linear-gradient(160deg, #e9e6de 0%, #b9b4a6 45%, #5d4a38 100%);
  }
  .photo-commercial-kitchen {
    left: 31px; top: 271px; width: 608px; height: 486px;
    background: linear-gradient(120deg, #b58a55 0%, #d4d6d8 28%, var(--steel-light) 55%, var(--steel-dark) 100%);
  }
  .accent-bar { position: absolute; left: 0; top: 271px; width: 31px; height: 486px; background: var(--brand-red); }
  .photo-wood-kitchen { left: 639px; top: 271px; width: 230px; height: 564px; }

  .seal-placeholder {
    position: absolute; left: 552px; top: 184px; width: 172px; height: 172px;
    border-radius: 50%; background: var(--seal-neutral); border: 6px solid var(--paper);
  }

  .headline {
    position: absolute; left: 53px; top: 800px; width: 700px;
    font-family: "Questrial", sans-serif; font-weight: 400;
    font-size: 29px; line-height: 35px; color: var(--ink-grey);
  }
  .body-copy {
    position: absolute; left: 53px; top: 878px; width: 745px;
    font-family: "Source Sans 3", sans-serif; font-weight: 400;
    font-size: 15.4px; line-height: 19px; color: var(--body-grey);
  }
  .body-copy p + p { margin-top: 19px; }

  .footer-band { position: absolute; left: 0; top: 1118px; width: 869px; height: 36px; background: var(--band-grey); }
  .partner-name {
    position: absolute; left: 56px; top: 1106px; width: 170px; height: 60px;
    display: flex; align-items: center; gap: 8px;
    font-family: "Source Sans 3", sans-serif; font-weight: 700;
    font-size: 17px; line-height: 19px; color: var(--brand-blue);
  }
  .partner-name .mark { flex: none; width: 16px; height: 16px; background: var(--brand-blue); }
  .contact {
    position: absolute; top: 1123px; display: flex; align-items: center; gap: 6px;
    font-family: "Source Sans 3", sans-serif; font-weight: 400;
    font-size: 19px; line-height: 26px; color: var(--brand-blue);
  }
  .contact-web { left: 312px; }
  .contact-phone { left: 651px; }
  .contact svg { width: 18px; height: 18px; }
</style>
</head>
<body>
<main class="flyer">
  <div class="brand-name"><span class="mark"></span>Brantley Services</div>

  <h1 class="title">Commercial Laundry<span class="accent">&amp; Dishwasher</span></h1>

  <div class="photo photo-home-kitchen" role="img" aria-label="Photo of a bright domestic kitchen with white cabinets and a range cooker"></div>
  <div class="accent-bar"></div>
  <div class="photo photo-commercial-kitchen" role="img" aria-label="Photo of a stainless steel commercial kitchen with cooking range and extraction hood"></div>
  <svg class="photo photo-wood-kitchen" viewBox="0 0 230 564" role="img" aria-label="Photo of a warm wooden kitchen with extractor hood, sink and gas hob">
    <defs>
      <linearGradient id="woodKitchen" x1="0" y1="0" x2="0" y2="1">
        <stop offset="0" stop-color="#c9b48a"/>
        <stop offset="0.45" stop-color="#8a5a34"/>
        <stop offset="1" stop-color="#2a201a"/>
      </linearGradient>
    </defs>
    <polygon points="0,0 230,0 230,564 0,486" fill="url(#woodKitchen)"/>
  </svg>

  <div class="seal-placeholder" role="img" aria-label="Anniversary seal"></div>

  <h2 class="headline">You trust us to repair your laundry equipment... why not trust us to do your catering equipment as well?</h2>

  <div class="body-copy">
    <p>Brantley Services Ltd specialise in the supply, installation &amp; maintenance of commercial Laundry &amp; Dishwashing equipment throughout the Midlands &amp; North West of England. Kestrel Catering Equipment Ltd is a fully owned subsidiary of Brantley Services. As independent suppliers they can recommend the full range of catering equipment to suit your needs from all of the major manufacturers.</p>
    <p>As an independent supplier for all of the major manufacturers, we are able to offer a full portfolio of machines, meaning we can tailor the equipment supplied to your specific requirements, these products are backed by our team of manufacturer trained engineers providing a prompt &amp; efficient repair service. Our engineers can provide preventative maintenance inspections and annual gas checks to ensure your legal and health &amp; safety compliance.</p>
  </div>

  <div class="footer-band"></div>
  <div class="partner-name"><span class="mark"></span>Kestrel Catering Equipment</div>
  <div class="contact contact-web">
    <svg viewBox="0 0 20 20" fill="none" stroke="currentColor" stroke-width="1.4"><circle cx="10" cy="10" r="8"/><ellipse cx="10" cy="10" rx="3.5" ry="8"/><line x1="2" y1="10" x2="18" y2="10"/><path d="M3.5 6h13M3.5 14h13"/></svg>
    www.brantleyservices-example.co.uk
  </div>
  <div class="contact contact-phone">
    <svg viewBox="0 0 20 20" fill="none" stroke="currentColor" stroke-width="1.4"><circle cx="10" cy="10" r="8.5"/><path d="M7 5.5l1.6 2.6-1 1.2a6 6 0 0 0 3.1 3.1l1.2-1 2.6 1.6-.8 1.8c-3.8.3-8.4-4.3-8.1-8.1z" fill="currentColor"/></svg>
    0116 583 2901
  </div>
</main>
</body>
</html>
```